Boutique custom software development company needs new business card

Our nearly 20 year old custom software development company would like to better include the fact that we are now providing Bitcoin services. These new services are B2B include education (how to acquire and securely hold Bitcoin) and integrating Bitcoin payments into existing ecommerce sites or other existing systems. Please keep the card clean and simple. Attached is our current design and some other files. vextorial.com

Target Market(s)

businesses owners interested in long term relationship

Industry/Entity Type

Custom software development and Bitcoin

Contact Information for Business Card

Dale Parker, dale@vextorial.com, vextorial.com, (888) 555-VXTRL

Font styles to use
Other font styles liked:
• monospace

Requirements
Must have
• double-sided
Nice to have
• clean and simple
Should not have
• physical address

```html
<!DOCTYPE html>
<html lang="en">
<head>
<meta charset="utf-8">
<title>Vextorial business card</title>
<link rel="stylesheet" href="https://fonts.googleapis.com/css2?family=Lato:wght@400;900&family=Roboto+Mono:wght@400;700&display=swap">
<style>
  :root {
    --bg: #e9e6e1;
    --card: #ffffff;
    --blue: #3d72b9;
    --orange: #ee7d24;
    --ink: #222222;
    --mark-tint: #f4f6fa;
  }
  * { box-sizing: border-box; margin: 0; padding: 0; }
  html, body { width: 900px; height: 1200px; overflow: hidden; background: var(--bg); }
  .canvas { position: relative; width: 900px; height: 1200px; }
  .card {
    position: absolute; left: 78px; width: 744px;
    background: var(--card); border-radius: 28px;
    box-shadow: 0 4px 10px rgba(0,0,0,0.18);
    overflow: hidden;
  }
  .card--front { top: 130px; height: 442px; }
  .card--back { top: 638px; height: 440px; }

  .brand-name {
    font-family: 'Lato', sans-serif; font-weight: 900;
    color: var(--blue); letter-spacing: 1px; line-height: 1;
    display: flex; align-items: center;
  }
  .brand-square { display: inline-block; background: var(--orange); }
  .tagline { font-family: 'Lato', sans-serif; font-weight: 400; color: var(--blue); letter-spacing: -0.5px; white-space: nowrap; }

  .card--front .brand-name { position: absolute; left: 26px; top: 30px; font-size: 54px; }
  .card--front .brand-square { width: 36px; height: 36px; margin-right: 12px; }
  .card--front .tagline { position: absolute; left: 40px; top: 104px; font-size: 22px; }

  .mono { font-family: 'Roboto Mono', monospace; color: var(--ink); }
  .services { position: absolute; left: 26px; top: 200px; font-size: 15.5px; line-height: 25px; list-style: none; }

  .mark-panel { position: absolute; left: 515px; top: 115px; width: 203px; height: 213px; background: var(--mark-tint); }
  .person { position: absolute; right: 26px; top: 190px; text-align: right; }
  .person-name { font-family: 'Roboto Mono', monospace; font-weight: 700; font-size: 28px; color: var(--orange); line-height: 1.1; }
  .person-role { font-size: 15.5px; margin-top: 6px; }
  .accent-bar { position: absolute; right: 0; top: 196px; width: 16px; height: 51px; background: var(--orange); }

  .contacts { position: absolute; left: 26px; top: 344px; list-style: none; font-size: 15.5px; }
  .contacts li { display: flex; align-items: center; height: 25px; }
  .contacts svg { width: 16px; height: 16px; margin-right: 8px; fill: var(--orange); }

  .card--back .logo-block { position: absolute; left: 0; right: 0; top: 118px; display: flex; flex-direction: column; align-items: center; }
  .card--back .brand-name { font-size: 106px; }
  .card--back .brand-square { width: 66px; height: 66px; margin-right: 20px; }
  .card--back .tagline { font-size: 44px; margin-top: 30px; }
</style>
</head>
<body>
<div class="canvas">
  <section class="card card--front">
    <div class="brand-name"><span class="brand-square"></span>VEXTORIAL</div>
    <div class="tagline">developer of custom applications</div>

    <ul class="services mono">
      <li>Custom software</li>
      <li>Bitcoin education</li>
      <li>Bitcoin payments</li>
    </ul>

    <div class="mark-panel"></div>
    <div class="person">
      <div class="person-name">Dale Parker</div>
      <div class="person-role mono">Founding Partner</div>
    </div>
    <div class="accent-bar"></div>

    <ul class="contacts mono">
      <li><svg viewBox="0 0 16 16"><path d="M2 5c0-2 2-3 6-3s6 1 6 3v1h-3V5H5v1H2z"/><path d="M4 7h8l2 6H2z"/></svg>(888) 555-VXTRL</li>
      <li><svg viewBox="0 0 16 16"><path d="M1 3h14v1L8 9 1 4z"/><path d="M1 6l7 5 7-5v7H1z"/></svg>dale@vextorial.com</li>
      <li><svg viewBox="0 0 16 16"><circle cx="8" cy="8" r="7"/><path d="M4 5h3v3H5zM9 9h3l-1 3H9z" fill="#fff"/></svg>www.vextorial.com</li>
    </ul>
  </section>

  <section class="card card--back">
    <div class="logo-block">
      <div class="brand-name"><span class="brand-square"></span>VEXTORIAL</div>
      <div class="tagline">developer of custom applications</div>
    </div>
  </section>
</div>
</body>
</html>
```